Web Design Project

8 page static website.
About us/What we stand for:
Forno Verdello CBD plans to make a huge splash in Sydney by being the first Italian pizza and pasta retail food outlet offering truly fresh, nutritious ingredients – herbs and vegetables are picked directly from the garden, pizzas are made with love in a fun filled atmosphere and a cutting edge brand strategy that promotes a happy lifestyle and reminds people that happiness and togetherness comes from sharing amazing food.
The best thing about Forno Verdello is that it offers consumers a choice to either choose from the enticing gluten free and vegetarian menu range to the more traditional pizza and pasta, we cater for their own tastes, this provides a distinct point of difference in the retail food market, as well as allowing consumers to have an endless range of choices without having to worry about the nutritional value.
Consumers have now become accustomed to a consistent brand experience which is setting increasingly high standards when it comes to food quality, taste and service.
We want to capitalise on the opportunity to create a strong, modern brand that promotes healthy lifestyle habits, sells fresh, wholesome ingredients, delivers
exceptional service in a fun filled atmosphere and appeals to a broad market.
Our business model is specifically pickup and delivery with a few seats and crates for eating in. It is for the time poor that still want to have a great tasting Italian experience with pizza and pasta within the quick service restaurant space. Takeaway, office catering and delivery will be a large percentage of our business.
Our philosophy at Forno Verdello is simple:
“Success is not a formula, it’s a recipe”.
Brand personality:
We are located in a laneway and basically the shop is a hole in the one. It looks like a restaurant you would see in Italy.
Modern Italian, contemporary, fun, rustic (Taco Brio, Brazed)
1 Aims of this website
• Emotionally connect with the target audience to reflect (“happiness and togetherness comes from sharing amazing food”)
• To entice people to order pizza
• To capture a mailing list
• To differentiate us from the low cost, low quality pizza
• To create a connection with the target audience, and promote word of mouth
2 Target audience(s)
• Male/Female
• 18-49
• Sydney CBD and Woolloomooloo
• Internet Savvy.
3. Contents/Functionality
www.crustlark.com.au – like the rustic brown in the website and the old washed out white colour through the font.
Target Market(s)
18-49 years old
City worker and resident
people that enjoy good food
Industry/Entity Type
Restaurant
Requirements
Must have
- Some splash of red and green to represent the italian theme.
Attached is a draft of the homepage layout.
Attached below are some fonts that we like.
Nice to have
- Please see http://www.brazedeats.com.au/Pages/locationmenu.aspx
This is how our takeaway menu looks like.

```html
<!DOCTYPE html>
<html lang="en">
<head>
<meta charset="utf-8">
<title>Forno Verdello</title>
<link rel="stylesheet" href="https://fonts.googleapis.com/css2?family=Schoolbell&family=Cabin+Sketch:wght@700&family=PT+Sans:wght@400;700&family=Open+Sans:wght@400;700&family=Arimo&display=swap">
<style>
:root{
  --wood-dark:#2a0508;
  --wood:#4a0a10;
  --wood-mid:#6a0f18;
  --black:#050203;
  --cream:#f4e3bf;
  --paper:#ecd7a8;
  --paper-edge:#c9a870;
  --red:#c8462a;
  --pin:#b8432a;
  --green:#3d9a2a;
  --nav-green:#b9d86a;
  --text-light:#e8e2dc;
  --frame:#d9d2cc;
  --hand:"Schoolbell","Comic Sans MS",cursive;
}
*{box-sizing:border-box;margin:0;padding:0}
html,body{width:831px;height:1200px;overflow:hidden;background:var(--black)}
h1,h2{font-weight:400}
.page{position:relative;width:831px;height:1200px;overflow:hidden;
  background:linear-gradient(180deg,var(--wood) 0,var(--wood-mid) 80px,var(--wood-dark) 160px,#1a0407 560px,var(--wood-dark) 620px,#140305 760px,var(--black) 790px,var(--black) 1110px,var(--wood-dark) 1120px,var(--wood) 1200px);
  font-family:"PT Sans",sans-serif;color:var(--text-light)}
.header-band{position:absolute;left:0;top:0;width:831px;height:160px;
  background:repeating-linear-gradient(180deg,rgba(0,0,0,0) 0,rgba(0,0,0,0) 14px,rgba(0,0,0,.25) 15px,rgba(0,0,0,0) 17px),linear-gradient(180deg,#5a0c14,#3a070c);
  border-bottom:2px solid #1a0306}
.brand{position:absolute;left:18px;top:22px;width:156px;height:128px;display:flex;align-items:center;justify-content:center;
  font-family:var(--hand);font-size:21px;color:var(--cream);text-align:center;line-height:1;white-space:nowrap}
.motto{position:absolute;left:240px;top:45px;width:352px;height:36px;background:rgba(30,3,6,.55);
  font-family:var(--hand);font-size:19px;color:var(--cream);text-align:center;line-height:36px;white-space:nowrap;overflow:hidden}
.share{position:absolute;left:684px;top:29px;font-family:"Arimo",sans-serif;font-size:9px;color:#ddd}
.share-icon{position:absolute;top:28px;width:12px;height:12px;border-radius:2px}
.hook{position:absolute;top:22px;width:6px;height:26px;border:2px solid #bbb;border-radius:3px}
.order{position:absolute;left:643px;top:47px;width:172px;height:30px;background:#f6f2ec;border-radius:3px;
  font-family:var(--hand);font-size:16px;color:#5a0a10;text-align:center;line-height:30px;white-space:nowrap;overflow:hidden;box-shadow:0 2px 3px rgba(0,0,0,.6)}
.nav{position:absolute;left:396px;top:108px;width:420px;height:36px;display:flex;justify-content:space-around;align-items:center;
  background:rgba(20,2,5,.35);list-style:none}
.nav a{font-family:var(--hand);font-size:16px;color:#f0e8e0;text-decoration:none;white-space:nowrap}
.nav a.active{color:var(--nav-green)}
.slider{position:absolute;left:17px;top:190px;width:797px;height:330px;border:2px solid var(--frame);border-radius:14px;padding:4px;background:#1a0306}
.slider-photo{width:100%;height:100%;border-radius:10px;
  background:radial-gradient(ellipse at 30% 45%,#f8f5ef 0,#e9dfcc 22%,#b08a3e 45%,#d9a53c 62%,#7a4a14 100%)}
.slider-title{position:absolute;left:470px;top:278px;width:330px;font-family:"Cabin Sketch",cursive;font-size:36px;line-height:42px;color:#f5f1ea;
  text-shadow:1px 1px 0 #222;transform:rotate(-6deg);text-align:center}
.slider-sub{position:absolute;left:500px;top:376px;width:300px;font-family:"Arimo",sans-serif;font-size:12.5px;color:#111;text-align:center;transform:rotate(-6deg)}
.dots{position:absolute;left:386px;top:531px;display:flex;gap:5px}
.dots span{width:11px;height:11px;border-radius:50%;background:#4a0a10;border:1px solid #2a0306}
.dots span.on{background:#bbb}
.welcome{position:absolute;left:0;top:568px;width:831px;text-align:center;font-family:var(--hand);font-size:18px;color:#fff;white-space:nowrap}
.rule{position:absolute;height:1px;background:#cfc6c0}
.intro{position:absolute;left:32px;top:638px;width:772px;font-size:12.4px;line-height:17px;color:#e6e0da;hyphens:auto}
.cards{position:absolute;left:13px;top:795px;width:810px;height:140px}
.card{position:absolute;top:0;width:196px;height:140px;background:radial-gradient(ellipse at 50% 50%,var(--cream),var(--paper) 70%,var(--paper-edge));
  font-family:"Open Sans",sans-serif}
.pin{position:absolute;left:8px;top:12px;width:28px;height:28px;border-radius:50%;background:var(--pin);border:2px solid #e8b89a}
.pin::after{content:"";position:absolute;left:8px;top:8px;width:8px;height:8px;border-radius:50%;background:#1a0606}
.card .kicker{position:absolute;left:42px;top:50px;font-size:12px;color:var(--green)}
.card .kicker b{font-weight:400;color:#222}
.card .heading{position:absolute;left:42px;top:66px;font-size:19px;font-weight:700;color:var(--red);white-space:nowrap}
.card .art{position:absolute;border-radius:6px}
.club .kicker{top:16px}
.club .heading{top:34px}
.club label{position:absolute;left:46px;font-size:9px;font-weight:700;color:#111}
.club .line{position:absolute;left:46px;width:144px;height:1px;background:#8a7a60}
.club .join{position:absolute;left:138px;top:108px;width:46px;height:16px;background:#f2f2f2;border:1px solid #999;font-size:9px;color:#222;text-align:center;line-height:14px}
.testimonials-title{position:absolute;left:30px;top:967px;font-family:var(--hand);font-size:18px;color:#fff}
.quote{position:absolute;top:1018px;width:260px;height:78px}
.quote .photo{position:absolute;left:0;top:0;width:80px;height:78px;border:2px solid #d9b27a;background:linear-gradient(135deg,#6aa0d8,#f0f0f0 50%,#c85a2a)}
.quote .name{position:absolute;left:88px;top:-2px;font-family:"Arimo",sans-serif;font-size:10px;color:#e03a2a}
.quote .place{position:absolute;left:88px;top:13px;font-family:"Arimo",sans-serif;font-size:10px;color:var(--green)}
.quote p{position:absolute;left:88px;top:28px;width:172px;font-family:"Arimo",sans-serif;font-size:10px;line-height:14px;color:#f0f0f0}
.vsep{position:absolute;top:1022px;width:1px;height:64px;background:#555}
.footer-nav{position:absolute;left:0;top:1148px;width:831px;text-align:center;font-size:10px;color:#e0d8d0}
.footer-nav a{color:#e0d8d0;text-decoration:none;margin:0 4px}
.copyright{position:absolute;left:0;top:1173px;width:831px;text-align:center;font-size:9.5px;color:#d8d0c8}
</style>
</head>
<body>
<div class="page">
  <header class="header-band">
    <div class="brand">Forno Verdello</div>
    <div class="motto">Success is not a formula, it’s a recipe</div>
    <span class="hook" style="left:657px"></span>
    <span class="hook" style="left:797px"></span>
    <span class="share">share</span>
    <span class="share-icon" style="left:730px;background:#2f6fc4"></span>
    <span class="share-icon" style="left:745px;background:#3aa0e0"></span>
    <span class="share-icon" style="left:760px;background:#e88a20"></span>
    <div class="order">Ordes now 9055301742</div>
    <ul class="nav">
      <li><a href="#" class="active">Home</a></li>
      <li><a href="#">About us</a></li>
      <li><a href="#">Menu</a></li>
      <li><a href="#">Contact us</a></li>
    </ul>
  </header>

  <section class="slider">
    <div class="slider-photo" role="img" aria-label="Close-up of a white espresso cup on a saucer with a spoon, warm golden background"></div>
  </section>
  <div class="slider-title">Lorem Ipsum is Simply dummy</div>
  <div class="slider-sub">Lorem Ipsum is simply dummy text of the printing and typesetting industry.</div>
  <div class="dots"><span></span><span class="on"></span><span></span><span></span></div>

  <div class="rule" style="left:0;top:551px;width:831px;background:#3a0a0e"></div>
  <div class="rule" style="left:280px;top:596px;width:270px"></div>
  <h2 class="welcome">Welcome To Forno Verdello</h2>
  <p class="intro">There are many variations of passages of Lorem Ipsum available, but the majority have suffered alteration in some form, by injected humour, or randomised words which don't look even slightly believable. If you are going to use a passage of Lorem Ipsum, you need to be sure there isn't anything embarrassing hidden in the middle of text. All the Lorem Ipsum generators on the Internet tend to repeat predefined chunks as necessary, making this the first true generator on the Internet. It uses a dictionary of over 200 Latin words, combined with a handful of model sentence structures, to generate Lorem Ipsum which looks reasonable</p>
  <div class="rule" style="left:280px;top:742px;width:270px"></div>
  <div class="rule" style="left:20px;top:768px;width:792px"></div>

  <section class="cards">
    <div class="card" style="left:0">
      <span class="pin"></span>
      <div class="kicker">Click <b>here to</b></div>
      <div class="heading">ORDER ONLINE</div>
      <div class="art" style="left:-8px;top:88px;width:62px;height:58px;border-radius:50%;background:radial-gradient(circle,#f3d890,#d9a040)" role="img" aria-label="Glazed pastry ring"></div>
    </div>
    <div class="card club" style="left:204px">
      <span class="pin"></span>
      <div class="kicker"><span style="color:var(--green)">Join</span> <b>Our</b></div>
      <div class="heading">EMAIL CLUB</div>
      <label style="top:66px">Name</label><span class="line" style="top:79px"></span>
      <label style="top:89px">Email</label><span class="line" style="top:102px"></span>
      <span class="join">Join</span>
      <div class="art" style="left:-4px;top:104px;width:44px;height:42px;background:linear-gradient(180deg,#e8e0d8 0,#e8e0d8 50%,#d39a20 50%)" role="img" aria-label="Member avatar with envelope icon"></div>
    </div>
    <div class="card" style="left:408px">
      <span class="pin"></span>
      <div class="kicker">Office</div>
      <div class="heading">CATERING</div>
      <div class="art" style="left:-4px;top:92px;width:66px;height:52px;background:linear-gradient(90deg,#bcd0e0 0,#bcd0e0 45%,#b87a40 45%)" role="img" aria-label="Office building with a cookie"></div>
    </div>
    <div class="card" style="left:612px">
      <span class="pin"></span>
      <div class="kicker">Delivery</div>
      <div class="heading">AREA</div>
      <div class="art" style="left:-6px;top:98px;width:70px;height:48px;background:linear-gradient(160deg,#d8c8a0,#8a7650)" role="img" aria-label="Folded delivery map"></div>
    </div>
  </section>

  <div class="rule" style="left:24px;top:961px;width:782px;background:#444"></div>
  <h2 class="testimonials-title">Testimonials</h2>
  <div class="rule" style="left:24px;top:1002px;width:782px;background:#444"></div>

  <div class="quote" style="left:26px">
    <div class="photo" role="img" aria-label="Customer portrait"></div>
    <div class="name">Marco Bellini</div><div class="place">USA</div>
    <p>" Lorem ipsum dolor sit amet,tetuer adipiscingelit, sed diam nonummy nibhismod tincidunt ut laoreetdo..."</p>
  </div>
  <span class="vsep" style="left:282px"></span>
  <div class="quote" style="left:297px">
    <div class="photo" role="img" aria-label="Customer portrait"></div>
    <div class="name">Marco Bellini</div><div class="place">USA</div>
    <p>" Lorem ipsum dolor sit amet,tetuer adipiscingelit, sed diam nonummy nibhismod tincidunt ut laoreetdo..."</p>
  </div>
  <span class="vsep" style="left:553px"></span>
  <div class="quote" style="left:566px">
    <div class="photo" role="img" aria-label="Customer portrait"></div>
    <div class="name">Marco Bellini</div><div class="place">USA</div>
    <p>" Lorem ipsum dolor sit amet,tetuer adipiscingelit, sed diam nonummy nibhismod tincidunt ut laoreetdo..."</p>
  </div>
  <div class="rule" style="left:20px;top:1110px;width:792px"></div>

  <footer>
    <nav class="footer-nav"><a href="#">Home</a>|<a href="#">About us</a>|<a href="#">Menu</a>|<a href="#">Contact us</a></nav>
    <div class="copyright">2011© Copyrights.forno verdello .Received</div>
  </footer>
</div>
</body>
</html>
```